Mortgage Company ready to make a statement!

We have a basic logo that I am fairly happy with ... but it could use a little bit of tweaking before we order the sign for our building. We also want some knock-your-socks-off business cards.
Problem: Inside of our Mortgage Office (Bright Fern Mortgage Group), we are going to have a coffee lounge (Sunbrew Cafe) for Realtors to use instead of the local Cuppington to meet with homebuyers. The office and coffee lounge are in an industrial building and is decorated with cozy overstuffed chairs, a hodge podge of interesting lamps and furniture, and goal is to make it as inviting as possible. However, we are a financial institution... so we need to keep it pretty clean as well.
One of my favorite marketing ideas is to cut a house key for everyone who buys a home using us with a key that matches our logo. There's only one key shape that works really well, so that needs to match the logo in order for the idea to work. I'll attach an image of the key blank.... although the way the key hole cut out looks terrible, so I was thinking of having them just do a thin outline instead.
Would like a similar, matching logo for the Sunbrew Cafe... but possibly something that would be a little less formal and would be cute on a coffee mug- nothing stuffy.
AND, we're opening a home inspection company as well, and we would like that logo and branding to match. The home inspection company is "Bright Fern Home Inspections"
We were thinking that for the home inspection company , we could use a magnifying glass shape inside of the house shape for the logo, use a keyhole shape inside of the same house for the mortgage company, and use a coffee cup inside of the house shape for Sunbrew Cafe.
Just getting stuck and need to help. I designed the attached logo myself, and that is what we are currently using. Designers at local printing companies have failed to impress us.
The mortgage industry has a lot of numbers and logos, etc that they require us to put on our business cards... so it's hard to keep them looking clean.
HELP! HELP! :)

```html
<!DOCTYPE html>
<html lang="en">
<head>
<meta charset="utf-8">
<title>Bright Fern Mortgage Group – Business Card</title>
<link rel="stylesheet" href="https://fonts.googleapis.com/css2?family=Marcellus&family=Poppins:wght@400;600&display=swap">
<style>
  :root {
    --page-bg: #ecebe6;
    --card-bg: #ffffff;
    --brand-blue: #1f5f86;
    --ink-dark: #3a3a3a;
    --ink-mid: #555555;
    --card-shadow: rgba(0, 0, 0, 0.28);
  }
  * { margin: 0; padding: 0; box-sizing: border-box; }
  html, body { width: 1200px; height: 929px; overflow: hidden; }
  body {
    background: var(--page-bg);
    position: relative;
    font-family: "Poppins", sans-serif;
  }
  .card {
    position: absolute;
    width: 520px;
    height: 297px;
    background: var(--card-bg);
    box-shadow: 3px 4px 8px var(--card-shadow);
  }
  .card--front { left: 90px; top: 120px; }
  .card--back { left: 590px; top: 500px; }

  /* Front */
  .brand {
    position: absolute;
    left: 0; right: 0; top: 104px;
    display: flex;
    align-items: center;
    justify-content: center;
    gap: 16px;
  }
  .brand__dot {
    width: 22px; height: 22px;
    background: var(--brand-blue);
  }
  .brand__name {
    font-family: "Marcellus", serif;
    color: var(--brand-blue);
    font-size: 34px;
    line-height: 1.05;
    letter-spacing: 0.5px;
  }
  .brand__name span { display: block; font-size: 22px; }

  /* Back */
  .person {
    position: absolute;
    right: 306px; top: 118px;
    text-align: right;
  }
  .person__name {
    font-family: "Marcellus", serif;
    color: var(--brand-blue);
    font-size: 22px;
    letter-spacing: 1px;
    white-space: nowrap;
  }
  .person__role {
    font-weight: 600;
    color: var(--ink-dark);
    font-size: 13px;
    margin-top: 2px;
  }
  .divider {
    position: absolute;
    left: 228px; top: 104px;
    width: 1px; height: 60px;
    background: var(--brand-blue);
  }
  .contact {
    position: absolute;
    left: 246px; top: 104px;
    list-style: none;
  }
  .contact li {
    display: flex;
    align-items: center;
    gap: 10px;
    font-size: 11px;
    color: var(--ink-mid);
    letter-spacing: 0.6px;
    height: 20px;
  }
  .contact svg { width: 10px; height: 10px; flex: none; }
  .address {
    position: absolute;
    left: 0; right: 0; bottom: 46px;
    text-align: center;
    font-size: 11px;
    color: var(--ink-mid);
    letter-spacing: 1px;
  }
</style>
</head>
<body>
  <section class="card card--front" aria-label="Card front">
    <div class="brand">
      <div class="brand__dot"></div>
      <div class="brand__name">BRIGHT FERN<span>Mortgage Group</span></div>
    </div>
  </section>

  <section class="card card--back" aria-label="Card back">
    <div class="person">
      <div class="person__name">DANA WHITLOW</div>
      <div class="person__role">CEO</div>
    </div>
    <div class="divider"></div>
    <ul class="contact">
      <li>
        <svg viewBox="0 0 10 10" aria-hidden="true"><rect x="2.5" y="0.5" width="5" height="9" rx="1" fill="none" stroke="#3a3a3a" stroke-width="1"/></svg>
        000-555-0148
      </li>
      <li>
        <svg viewBox="0 0 10 10" aria-hidden="true"><rect x="2.5" y="0.5" width="5" height="3" fill="#3a3a3a"/><rect x="0.5" y="3.5" width="9" height="4" rx="1" fill="#3a3a3a"/><rect x="2.5" y="6.5" width="5" height="3" fill="#fff" stroke="#3a3a3a" stroke-width="1"/></svg>
        000-555-0149
      </li>
      <li>
        <svg viewBox="0 0 10 10" aria-hidden="true"><rect x="0.5" y="2" width="9" height="6" fill="#3a3a3a"/><path d="M0.5 2 L5 5.5 L9.5 2" fill="none" stroke="#fff" stroke-width="0.8"/></svg>
        dana.whitlow@brightfern.example
      </li>
    </ul>
    <div class="address">Harbour Point Centre Adelaide</div>
  </section>
</body>
</html>
```